Dynamic Business Card for Sports Supplements Company

Hi! I'm looking for an awesome business card to match my existing sports supplement company. I have uploaded my current company logo and screenshot of the front page of my website.

I would like to have something dynamic and interesting and utilize the colors in the website - the reds and purples

The business card should be double sided and focus on a unique eye-catching design on the back and include all the relevant company info.

Most importantly, it should say somewhere: "Sign up on our website for a coupon code."

Target Market(s)

Mostly for women gym goers but it shouldn't be too feminine. It should be in keeping with the website design. It should flow and clearly be connected to it

Industry/Entity Type

Business

Contact Information for Business Card

Lorraine K. Vestal
CEO
LVestal@Quorvanexco.com
www.quorvanexco.com
555.417.3820
P.O. Box 47315
Fenwick Cove, Ohio 00000

Sign up on our website for a coupon code

Font styles to use
Serif
Sans Serif
Other font styles liked:
• Novecento font family and "Quorvanex" is in AR Destine font

Requirements
Must have
• One side should be a bold Quorvanex logo design. Even just the symbol itself may be o.k. (see attached file)

```html
<!DOCTYPE html>
<html lang="en">
<head>
<meta charset="utf-8">
<title>Quorvanex Business Card</title>
<link href="https://fonts.googleapis.com/css2?family=Open+Sans:wght@400;600;700&display=swap" rel="stylesheet">
<style>
  :root {
    --backdrop: #d6d6d6;
    --card-black: #0b0b0b;
    --brand-red: #e21f26;
    --paper: #efefef;
    --paper-shade: #e2e2e2;
    --ink: #1e1e1e;
    --white: #ffffff;
  }
  * { margin: 0; padding: 0; box-sizing: border-box; }
  html, body {
    width: 1200px; height: 900px; overflow: hidden;
    background: var(--backdrop);
    font-family: "Open Sans", Arial, sans-serif;
  }
  .business-card {
    position: absolute; left: 120px; top: 153px;
    width: 960px; height: 594px;
    display: flex;
    box-shadow: 0 14px 40px rgba(0,0,0,0.22);
  }
  .brand-panel {
    position: relative;
    width: 484px; height: 100%;
    background: var(--card-black);
    color: var(--white);
    text-align: center;
  }
  .brand-mark {
    position: absolute; left: 197px; top: 150px;
    width: 90px; height: 90px;
    background: var(--brand-red);
  }
  .brand-name {
    position: absolute; left: 0; right: 0; top: 300px;
    font-weight: 700; font-size: 46px; letter-spacing: 2px;
    line-height: 1;
  }
  .brand-tagline {
    position: absolute; left: 0; right: 0; top: 358px;
    font-weight: 400; font-size: 16px; letter-spacing: 1.5px;
  }
  .coupon-callout {
    position: absolute; left: 0; right: 0; top: 418px;
    font-size: 26px; line-height: 35px; font-weight: 400;
  }
  .divider-stripe {
    width: 10px; height: 100%;
    background: var(--brand-red);
  }
  .contact-panel {
    position: relative; flex: 1; height: 100%;
    background: radial-gradient(ellipse at 40% 30%, var(--paper) 0%, var(--paper-shade) 100%);
    color: var(--ink);
  }
  .person-name {
    position: absolute; left: 37px; top: 140px;
    color: var(--brand-red); font-size: 35px; font-weight: 400; letter-spacing: 0.5px;
  }
  .person-title {
    position: absolute; left: 37px; top: 188px;
    font-size: 24px;
  }
  .contact-list { position: absolute; left: 37px; top: 248px; list-style: none; }
  .contact-list li {
    display: flex; align-items: center; gap: 12px;
    font-size: 24px; line-height: 35px;
  }
  .contact-list svg { width: 17px; height: 17px; fill: var(--brand-red); flex: none; }
  .mailing-address {
    position: absolute; left: 37px; top: 373px;
    font-size: 24px; line-height: 35px; font-style: normal;
  }
</style>
</head>
<body>
  <div class="business-card">
    <section class="brand-panel">
      <div class="brand-mark"></div>
      <div class="brand-name">QUORVANEX</div>
      <div class="brand-tagline">YOUR TRAINING COMPANION</div>
      <p class="coupon-callout">SIGN UP ON OUR WEBSITE<br>FOR A COUPON CODE</p>
    </section>
    <div class="divider-stripe"></div>
    <section class="contact-panel">
      <h1 class="person-name">LORRAINE K. VESTAL</h1>
      <p class="person-title">CEO</p>
      <ul class="contact-list">
        <li>
          <svg viewBox="0 0 24 24" aria-hidden="true"><path d="M6.6 10.8a15.1 15.1 0 0 0 6.6 6.6l2.2-2.2c.3-.3.7-.4 1-.2 1.1.4 2.3.6 3.6.6.6 0 1 .4 1 1V20c0 .6-.4 1-1 1A17 17 0 0 1 3 4c0-.6.4-1 1-1h3.5c.6 0 1 .4 1 1 0 1.3.2 2.5.6 3.6.1.3 0 .7-.2 1z"/></svg>
          555.417.3820
        </li>
        <li>
          <svg viewBox="0 0 24 24" aria-hidden="true"><path d="M2 5h20v2l-10 6L2 7zM2 9l10 6 10-6v10H2z"/></svg>
          LVestal@Quorvanexco.com
        </li>
        <li>
          <svg viewBox="0 0 24 24" aria-hidden="true"><circle cx="12" cy="12" r="10"/><path d="M7 9l3-2 2 2-1 3 3 1v4l-3 1-1-3-3-2z" fill="#efefef"/></svg>
          www.quorvanexco.com
        </li>
      </ul>
      <address class="mailing-address">P.O. Box 47315<br>Fenwick Cove, Ohio 00000</address>
    </section>
  </div>
</body>
</html>
```